Coastal Learner Bureau business cards

Australian company about to start offering its services. We recruit international students to come to study English, vocational education and postgraduate courses in Australia. We help them find the institution and select the right city they want to come to Australia. We are a young, online oriented and supportive agency. Our clients are between 18 and 35 years old, mainly University students, young professionals or people with work experience. We provide much more information that any other agency offer. We administrate a Facebook group with more than 11.000 members that daily ask questions about general information when coming to Australia, while they are here and even after they leave the country

Target Market(s)

International students from South America, Central America and Europe

Industry/Entity Type

Student

Contact Information for Business Card

Tomas Bilbrea
Managing Director
tomas@kelvarin.com.au
www.kelvoria.com.au
+61 491058264
Melbourne, Australia

Font styles to use
Serif
Sans Serif

Colors

Designer to choose colors to be used in the design.

Requirements
Must have
• Horizontal design
• Standard business card size and shape. If font uses green or yellow colours, they will have to match the ones from the logo
Nice to have
• UPDATE: Use the contents of the green image to design one of the card sides. Use our logo in the background of that side as watermark.
• Passport image, or immigration stamps. A picture of the Yarra River (from Melbourne) would be cool as well.
Should not have
• Non-standard business card size and shape
• Not black as the background colour of any sides as we are not a VIP agency or a hight class service. We are orientes to young people and they like colours, pictures, something attractive.
• Vertical design
• NO YELLOW or BLACK AS THE BACKGROUND COLOUR OF ANY SIDE OF THE BIZ CARD

```html
<!DOCTYPE html>
<html lang="en">
<head>
<meta charset="utf-8">
<title>Coastal Learner Bureau – Business Cards</title>
<link href="https://fonts.googleapis.com/css2?family=Ubuntu:wght@500;700&family=Open+Sans:ital,wght@0,400;1,700&display=swap" rel="stylesheet">
<style>
  :root {
    --green: #14603f;
    --green-light: #1a8a5b;
    --green-dark: #0e5438;
    --yellow: #e8bf16;
    --paper: #f4f4f3;
    --ink: #555a57;
    --rule: #c9c9c7;
    --stage: #ece9e4;
  }
  * { margin: 0; padding: 0; box-sizing: border-box; }
  html, body { width: 1200px; height: 960px; overflow: hidden; }
  body { background: var(--stage); position: relative; font-family: "Open Sans", Arial, sans-serif; }

  .card {
    position: absolute;
    width: 600px;
    height: 342px;
    border-radius: 22px;
    overflow: hidden;
    box-shadow: 0 4px 10px rgba(0,0,0,0.25);
  }

  /* Front */
  .card-front { left: 302px; top: 129px; background: var(--paper); }
  .card-front .swoosh { position: absolute; left: 0; bottom: 0; width: 600px; height: 342px; }
  .brand-mark {
    position: absolute; left: 86px; top: 105px; width: 200px;
    font-family: "Ubuntu", sans-serif; font-weight: 700;
    font-size: 30px; line-height: 34px; color: var(--green);
  }
  .divider { position: absolute; left: 316px; top: 86px; width: 1px; height: 156px;
    background: linear-gradient(to bottom, transparent, var(--rule) 20%, var(--rule) 80%, transparent); }
  .contact { position: absolute; left: 343px; top: 94px; }
  .contact .name { font-family: "Ubuntu", sans-serif; font-weight: 700; font-size: 21px; color: var(--green); line-height: 26px; }
  .contact .role { font-family: "Ubuntu", sans-serif; font-weight: 500; font-size: 14px; color: var(--yellow); line-height: 18px; }
  .contact .city { font-size: 13px; color: var(--ink); margin-top: 12px; line-height: 18px; }
  .contact ul { list-style: none; margin-top: 8px; }
  .contact li { font-size: 13px; color: var(--ink); line-height: 19px; display: flex; align-items: center; }
  .contact li svg { width: 12px; height: 12px; margin-right: 10px; fill: var(--green); flex: none; }

  /* Back */
  .card-back { left: 299px; top: 488px; background: linear-gradient(135deg, var(--green-light) 0%, var(--green) 45%, var(--green-dark) 100%); }
  .card-back .brand-mark-large {
    position: absolute; left: 0; right: 0; top: 130px; text-align: center;
    font-family: "Ubuntu", sans-serif; font-weight: 700; font-size: 44px; color: #fff;
  }
  .tagline {
    position: absolute; left: 115px; width: 370px; top: 296px;
    display: flex; align-items: center; gap: 6px;
    font-style: italic; font-weight: 700; font-size: 14px; color: #fff; white-space: nowrap;
  }
  .tagline::before, .tagline::after { content: ""; flex: 1; height: 1px; }
  .tagline::before { background: linear-gradient(to right, transparent, rgba(255,255,255,0.8)); }
  .tagline::after { background: linear-gradient(to left, transparent, rgba(255,255,255,0.8)); }
</style>
</head>
<body>
  <section class="card card-front">
    <div class="brand-mark">Coastal Learner Bureau</div>
    <div class="divider"></div>
    <div class="contact">
      <p class="name">Tomas Bilbrea</p>
      <p class="role">Managing Director</p>
      <p class="city">Melbourne, Australia</p>
      <ul>
        <li><svg viewBox="0 0 12 12"><path d="M2.5 0.8l2 2.3-1 1.4c.7 1.5 1.9 2.7 3.4 3.4l1.4-1 2.3 2-1.3 2.1C5.1 10.8 1.2 6.9 .4 2.1z"/></svg>+61 491058264</li>
        <li><svg viewBox="0 0 12 12"><path d="M0 2h12v1L6 7 0 3z M0 4.3l6 4 6-4V10H0z"/></svg>tomas@kelvarin.com.au</li>
        <li><svg viewBox="0 0 12 12"><circle cx="6" cy="6" r="6"/></svg>www.kelvoria.com.au</li>
      </ul>
    </div>
    <svg class="swoosh" viewBox="0 0 600 342" aria-hidden="true">
      <path d="M0 284 Q250 330 600 300 L600 342 L0 342 Z" fill="#ffffff"/>
      <path d="M0 282 Q250 322 600 297 Q300 334 0 300 Z" fill="var(--yellow)"/>
      <path d="M0 306 Q280 340 600 302 L600 342 L0 342 Z" fill="var(--green)"/>
    </svg>
  </section>

  <section class="card card-back">
    <div class="brand-mark-large">Coastal Learner Bureau</div>
    <p class="tagline">Hacemos más por ti!</p>
  </section>
</body>
</html>
```